Business card for denture clinic Veltrimora

We need a new business card with our new logo. We are a denture clinic in New Zealand with our target market being 45+ years old. We would need a space on the back to write our patients next appointment on. We would space for only one appointment rather than a list. We will attach a photo showing an example of this. But of course, we would like to see your twist on this. We want it to be bold and easy to read and a good mixture of professional but modern. We have attached our logo to be used on the card.

Target Market(s)

People aged 45+ needing dentures

Industry/Entity Type

Dental

Contact Information for Business Card

We want our logo on the front and the space to write an appointment on the back. I've attached an example our our old business card showing this. We need to have the technicians details on the front.

Font styles to use
Sans Serif

Colors
0255a3
919191
fbfbfb

Requirements
Must have
• The following details:
• Liam Dorsett BDT, PGDipCDentTech Calverin
• Dental Prosthetist
• Phone numbers: 0800 47 3125
• 09 572 1394
• Email: liam@veltrimora.co.nz
• www.veltrimora.co.nz
• Address: 14 Marlow Crest Road
• Halbrook West
• Auckland 0793
Nice to have
• We would like our business cards to have more than just two colours as we want them to be more vibrant. We have uploaded an example of a business card we liked that showed this.

```html
<!DOCTYPE html>
<html lang="en">
<head>
<meta charset="utf-8">
<title>Veltrimora Business Card</title>
<link rel="stylesheet" href="https://fonts.googleapis.com/css2?family=Open+Sans:ital,wght@0,400;0,600;0,700;1,400&display=swap">
<style>
  :root {
    --brand-blue: #0255a3;
    --mid-blue: #0a6dbf;
    --brand-grey: #919191;
    --paper: #fbfbfb;
    --backdrop: #262626;
    --ink-muted: #5c5c5c;
    --dots: #6b6b6b;
  }
  * { box-sizing: border-box; margin: 0; padding: 0; }
  html, body { width: 1200px; height: 987px; overflow: hidden; }
  body {
    background: var(--backdrop);
    font-family: "Open Sans", Arial, sans-serif;
    position: relative;
  }
  .card {
    position: absolute;
    left: 293px;
    width: 615px;
    height: 352px;
    background: var(--paper);
    overflow: hidden;
  }
  .card--front { top: 130px; }
  .card--back { top: 505px; }

  /* Front */
  .wave { position: absolute; inset: 0; width: 100%; height: 100%; }
  .brand-mark {
    position: absolute; left: 157px; top: 49px;
    width: 59px; height: 59px; background: var(--mid-blue);
  }
  .brand-name {
    position: absolute; left: 48px; top: 106px; width: 275px;
    text-align: center;
    font-size: 27px; font-weight: 600; letter-spacing: 1.5px;
    color: var(--mid-blue);
  }
  .brand-tagline {
    position: absolute; left: 86px; top: 143px; width: 202px;
    text-align: center;
    font-size: 10.5px; letter-spacing: 2.6px; color: var(--brand-grey);
  }
  .technician {
    position: absolute; left: 22px; top: 270px; color: #fff;
  }
  .technician__name {
    font-size: 18px; font-weight: 600; line-height: 25px;
  }
  .technician__role { font-size: 16px; line-height: 24px; }
  .contact {
    position: absolute; right: 17px; top: 197px;
    color: #fff; text-align: right; font-size: 15px;
  }
  .contact__address { line-height: 20px; margin-bottom: 7px; }
  .contact__line {
    display: flex; justify-content: flex-end; align-items: center;
    gap: 7px; height: 24px;
  }
  .contact__line--small { font-size: 14px; }
  .contact__line svg { width: 16px; height: 16px; flex: none; }

  /* Back */
  .appointment__title {
    position: absolute; left: 0; right: 0; top: 28px;
    text-align: center; color: var(--mid-blue);
    font-size: 22px; font-weight: 600;
  }
  .field {
    position: absolute; display: flex; align-items: baseline;
    color: var(--mid-blue); font-size: 16px;
  }
  .field__rule {
    flex: 1; border-bottom: 2px dotted var(--dots);
    margin-left: 6px; transform: translateY(-3px);
  }
  .field--name { left: 32px; top: 86px; width: 534px; }
  .field--date { left: 30px; top: 130px; width: 283px; }
  .field--time { left: 341px; top: 130px; width: 165px; }
  .field__suffix { position: absolute; left: 518px; top: 135px; font-size: 12px; color: var(--mid-blue); }
  .field--note { left: 35px; top: 218px; width: 531px; }
  .note-rule {
    position: absolute; left: 33px; top: 263px; width: 533px;
    border-bottom: 2px dotted var(--dots);
  }
  .weekdays {
    position: absolute; left: 33px; top: 179px; width: 545px;
    display: flex; justify-content: space-between;
    color: var(--mid-blue); font-size: 15px;
  }
  .weekday { display: flex; align-items: center; gap: 4px; }
  .weekday__box {
    width: 17px; height: 14px; border: 1.5px solid var(--mid-blue);
  }
  .cancellation {
    position: absolute; left: 0; right: 0; top: 295px;
    text-align: center; font-style: italic; font-size: 13px;
    line-height: 18px; color: var(--ink-muted);
  }
</style>
</head>
<body>

<section class="card card--front" aria-label="Business card front">
  <svg class="wave" viewBox="0 0 525 300" preserveAspectRatio="none" aria-hidden="true">
    <path d="M0,162 C70,200 170,226 262,214 C170,220 70,198 0,182 Z" fill="var(--brand-grey)"/>
    <path d="M230,212 C330,200 420,112 525,106 L525,113 C425,122 330,205 230,212 Z" fill="var(--mid-blue)"/>
    <path d="M0,187 C110,232 250,228 340,172 C410,130 465,114 525,116 L525,300 L0,300 Z" fill="var(--mid-blue)"/>
  </svg>

  <div class="brand-mark" aria-hidden="true"></div>
  <div class="brand-name">VELTRIMORA</div>
  <div class="brand-tagline">THE DENTURE EXPERTS</div>

  <div class="contact">
    <div class="contact__address">14 Marlow Crest Road<br>Halbrook West, Auckland 0793</div>
    <div class="contact__line">0800 47 3125
      <svg viewBox="0 0 16 16" aria-hidden="true"><path d="M2,6 C2,3 5,2 8,2 C11,2 14,3 14,6 L11,6 L10,4.5 L6,4.5 L5,6 Z M4,8 L12,8 L13,14 L3,14 Z" fill="#fff"/><circle cx="8" cy="11" r="1.6" fill="var(--mid-blue)"/></svg>
    </div>
    <div class="contact__line">09 572 1394
      <svg viewBox="0 0 16 16" aria-hidden="true"><rect x="4" y="1" width="8" height="14" rx="1.5" fill="#fff"/><rect x="5.5" y="3" width="5" height="8.5" fill="var(--mid-blue)"/></svg>
    </div>
    <div class="contact__line contact__line--small">liam@veltrimora.co.nz
      <svg viewBox="0 0 16 16" aria-hidden="true"><rect x="1" y="4" width="14" height="9" fill="#fff"/><path d="M1,4 L8,9.5 L15,4" fill="none" stroke="var(--mid-blue)" stroke-width="1.2"/></svg>
    </div>
    <div class="contact__line contact__line--small">www.veltrimora.co.nz
      <svg viewBox="0 0 16 16" aria-hidden="true"><circle cx="8" cy="8" r="7" fill="#fff"/><path d="M5,4 L8,6 L7,9 L9,12 M10,3 L11,6 L13,7" fill="none" stroke="var(--mid-blue)" stroke-width="1.4"/></svg>
    </div>
  </div>

  <div class="technician">
    <div class="technician__name">Liam Dorsett BDT,<br>PGDipCDentTech Calverin</div>
    <div class="technician__role">Dental Prosthetist</div>
  </div>
</section>

<section class="card card--back" aria-label="Business card back">
  <h1 class="appointment__title">Next Appointment</h1>

  <div class="field field--name">Name :<span class="field__rule"></span></div>
  <div class="field field--date">Date :<span class="field__rule"></span></div>
  <div class="field field--time">Time :<span class="field__rule"></span></div>
  <span class="field__suffix">AM/PM</span>

  <div class="weekdays">
    <span class="weekday">Sun<span class="weekday__box"></span></span>
    <span class="weekday">Mon<span class="weekday__box"></span></span>
    <span class="weekday">Tue<span class="weekday__box"></span></span>
    <span class="weekday">Wed<span class="weekday__box"></span></span>
    <span class="weekday">Thu<span class="weekday__box"></span></span>
    <span class="weekday">Fri<span class="weekday__box"></span></span>
    <span class="weekday">Sat<span class="weekday__box"></span></span>
  </div>

  <div class="field field--note">Note :<span class="field__rule"></span></div>
  <div class="note-rule"></div>

  <p class="cancellation">Please give me 24 hours notice if you are unable to keep your appointment or<br>a cancellation fee may be charged.</p>
</section>

</body>
</html>
```